Business card design for Automotive workshop

We need a business card for a new automotive repair and tyre shop called Keelstone Prime Automotive located in New Zealand. We are a clean, modern and fresh workshop and company.

Front needs to feature logo,
my name:
Marlo Fenwicke (director)

Address:
48 Tarn Lane
Korowai Bay 3592

Phone: 07 594 2713
Mobile: 027 451 9362
Email: office@keelstoneautomotive.example.nz
Website: keelstoneautomotive.example.nz

Back needs to feature an area to write down appointment details, date and time.

Also feature a list of jobs and work we do such as,
Vehicle Servicing
All Mechanical Repairs
Warrant of Fitness
Tyres & Wheel Alignments
Automotive Diagnostics
Automotive Parts & Supplies

```html
<!DOCTYPE html>
<html lang="en">
<head>
<meta charset="utf-8">
<title>Keelstone Prime Automotive – Business Card</title>
<link href="https://fonts.googleapis.com/css2?family=Open+Sans:wght@400;600;700&display=swap" rel="stylesheet">
<style>
  :root {
    --card-black: #0b0b0b;
    --brand-red: #e3232f;
    --paper-white: #ffffff;
    --backdrop: #d9d6d0;
  }
  * { box-sizing: border-box; margin: 0; padding: 0; }
  html, body { width: 1200px; height: 903px; overflow: hidden; }
  body {
    background: var(--backdrop);
    font-family: "Open Sans", Arial, sans-serif;
    position: relative;
  }
  .card {
    position: absolute;
    width: 620px;
    height: 354px;
    background: var(--card-black);
    overflow: hidden;
    color: var(--paper-white);
  }
  .card--back { left: 120px; top: 60px; }
  .card--front { left: 460px; top: 490px; }
  .card__band { position: absolute; inset: 0; }

  .wordmark {
    position: absolute;
    display: flex;
    align-items: center;
    gap: 12px;
  }
  .wordmark__square {
    width: 16px; height: 16px;
    background: var(--brand-red);
  }
  .wordmark__name {
    color: var(--brand-red);
    font-weight: 700;
    text-transform: uppercase;
    font-size: 24px;
    line-height: 1.05;
    letter-spacing: 1px;
  }
  .card--back .wordmark { left: 180px; top: 50px; }
  .card--front .wordmark { left: 44px; top: 40px; }

  .services {
    position: absolute;
    left: 44px; top: 168px;
    list-style: none;
    font-size: 17px;
    line-height: 25px;
  }
  .services li::before {
    content: "";
    display: inline-block;
    width: 5px; height: 5px;
    background: var(--brand-red);
    margin-right: 6px;
    vertical-align: middle;
  }

  .appointment {
    position: absolute;
    left: 340px; top: 168px;
  }
  .appointment__row {
    display: flex;
    align-items: center;
    gap: 10px;
    margin-bottom: 14px;
  }
  .appointment__row:nth-child(2) { margin-left: 40px; }
  .appointment__label {
    color: var(--brand-red);
    font-size: 15px;
    width: 40px;
  }
  .appointment__field {
    width: 170px; height: 26px;
    background: var(--paper-white);
    border-radius: 13px;
  }

  .person {
    position: absolute;
    left: 44px; top: 136px;
  }
  .person__name { font-size: 20px; font-weight: 700; }
  .person__title { font-size: 14px; color: var(--brand-red); }

  .contacts {
    position: absolute;
    left: 44px; top: 204px;
    list-style: none;
    font-size: 15px;
    line-height: 21px;
  }
  .contacts li { display: flex; align-items: center; gap: 8px; }
  .contacts svg { width: 13px; height: 13px; flex: none; }
</style>
</head>
<body>

<section class="card card--back" aria-label="Card back: services and appointment">
  <svg class="card__band" viewBox="0 0 620 354" aria-hidden="true">
    <rect x="0" y="330" width="372" height="24" fill="var(--brand-red)"/>
    <polygon points="378,354 392,330 404,330 390,354" fill="var(--paper-white)"/>
    <polygon points="396,354 410,330 422,330 408,354" fill="var(--paper-white)"/>
    <polygon points="414,354 428,330 620,330 620,354" fill="var(--brand-red)"/>
    <rect x="330" y="262" width="290" height="20" fill="var(--brand-red)"/>
  </svg>
  <div class="wordmark">
    <span class="wordmark__square"></span>
    <span class="wordmark__name">Keelstone Prime<br>Automotive</span>
  </div>
  <ul class="services">
    <li>Vehicle Servicing</li>
    <li>All Mechanical Repairs</li>
    <li>Warrant of Fitness</li>
    <li>Tyres &amp; Wheel Alignments</li>
    <li>Automotive Diagnostics</li>
    <li>Automotive Parts &amp; Supplies</li>
  </ul>
  <div class="appointment">
    <div class="appointment__row"><span class="appointment__label">Date</span><span class="appointment__field"></span></div>
    <div class="appointment__row"><span class="appointment__label">Time</span><span class="appointment__field"></span></div>
  </div>
</section>

<section class="card card--front" aria-label="Card front: contact details">
  <svg class="card__band" viewBox="0 0 620 354" aria-hidden="true">
    <rect x="0" y="330" width="372" height="24" fill="var(--brand-red)"/>
    <polygon points="378,354 392,330 404,330 390,354" fill="var(--paper-white)"/>
    <polygon points="396,354 410,330 422,330 408,354" fill="var(--paper-white)"/>
    <polygon points="414,354 428,330 620,330 620,354" fill="var(--brand-red)"/>
    <rect x="400" y="236" width="220" height="20" fill="var(--brand-red)"/>
  </svg>
  <div class="wordmark">
    <span class="wordmark__square"></span>
    <span class="wordmark__name">Keelstone Prime<br>Automotive</span>
  </div>
  <div class="person">
    <p class="person__name">Marlo Fenwicke</p>
    <p class="person__title">Managing Director</p>
  </div>
  <ul class="contacts">
    <li><svg viewBox="0 0 12 12"><rect x="3" y="0.5" width="6" height="11" rx="1" fill="none" stroke="var(--brand-red)" stroke-width="1.2"/></svg>+ 027 451 9362</li>
    <li><svg viewBox="0 0 12 12"><path d="M1 5 Q6 0 11 5 L9 6 L8 4 H4 L3 6 Z M2 7 H10 V11 H2 Z" fill="var(--brand-red)"/></svg>+ 07 594 2713</li>
    <li><svg viewBox="0 0 12 12"><rect x="0.5" y="2" width="11" height="8" fill="var(--brand-red)"/><path d="M0.5 2 L6 7 L11.5 2" fill="none" stroke="var(--card-black)" stroke-width="1"/></svg>office@keelstoneautomotive.example.nz</li>
    <li><svg viewBox="0 0 12 12"><rect x="0.5" y="1" width="11" height="8" fill="none" stroke="var(--brand-red)" stroke-width="1.2"/><rect x="4" y="10" width="4" height="1.5" fill="var(--brand-red)"/></svg>keelstoneautomotive.example.nz</li>
    <li><svg viewBox="0 0 12 12"><path d="M6 11.5 C6 11.5 2 7 2 4.5 A4 4 0 0 1 10 4.5 C10 7 6 11.5 6 11.5 Z" fill="var(--brand-red)"/><circle cx="6" cy="4.5" r="1.4" fill="var(--card-black)"/></svg>48 Tarn Lane, Korowai Bay 3592</li>
  </ul>
</section>

</body>
</html>
```